Vorn upkeep KT Solar Venture

Solar power system install
Services and maintenance
wiring, Rewinding and Renovation
Switch Board Upgrade
Power and lighting point
t doesn’t matter how much you spend on quality parts, your solar system will let you down if your design and installation are sub-par. Have your solar system tailored and installed by our Master Electrician and Bright Grid Guild Accredited team.

Target Market(s)

sales and installed

Industry/Entity Type

Solar install and retailer

Contact Information for Business Card

Name , Email, Phone Number ,Business address,

Font styles to use
Serif

Colors
0054AA
0677BA
7BADD7
CADEEF
E8F1F8

Requirements
Must have
• clear and bright
Nice to have
• new design
Should not have
• unclear pictures

```html
<!DOCTYPE html>
<html lang="en">
<head>
<meta charset="utf-8">
<title>Vorn Upkeep KT Solar Venture – Business Card</title>
<link rel="stylesheet" href="https://fonts.googleapis.com/css2?family=Source+Serif+4:wght@400;600;700&display=swap">
<style>
  :root {
    --page-bg: #2e2e2e;
    --brand-blue: #0054AA;
    --brand-mid: #0677BA;
    --teal: #1f8f95;
    --green: #5fae3a;
    --leaf-green: #2e8b3a;
    --band: #e9ecef;
    --card-white: #f1f1f1;
    --ink: #1e1e1e;
    --white: #ffffff;
  }
  * { margin: 0; padding: 0; box-sizing: border-box; }
  html, body { width: 1200px; height: 1138px; overflow: hidden; }
  body {
    background: var(--page-bg);
    font-family: "Source Serif 4", Georgia, serif;
    position: relative;
  }
  .card {
    position: absolute;
    width: 620px;
    height: 375px;
    border-radius: 16px;
    overflow: hidden;
  }
  .card-front {
    left: 274px; top: 186px;
    background: linear-gradient(100deg, var(--brand-mid) 0%, var(--teal) 45%, var(--green) 100%);
  }
  .front-brand {
    position: absolute; left: 100px; top: 72px;
    display: flex; align-items: center; gap: 18px;
  }
  .brand-dot {
    width: 86px; height: 86px; border-radius: 50%;
    background: var(--white); opacity: .9; flex: none;
  }
  .brand-name {
    font-family: "Source Serif 4", Georgia, serif;
    font-weight: 700;
    font-size: 30px;
    line-height: 1.15;
    letter-spacing: .5px;
    text-transform: uppercase;
  }
  .card-front .brand-name { color: var(--white); }
  .services-band {
    position: absolute; left: 0; top: 239px;
    width: 100%; height: 74px;
    background: var(--band);
    display: flex; flex-direction: column; justify-content: center; align-items: center;
    color: var(--ink); font-size: 15.5px; line-height: 1.45; white-space: nowrap;
  }
  .site-row {
    position: absolute; left: 0; top: 331px; width: 100%;
    display: flex; justify-content: center; align-items: center; gap: 26px;
    color: var(--white); font-size: 16px;
  }
  .site-row .rule { width: 80px; height: 2px; background: rgba(255,255,255,.75); }
  .card-back {
    left: 276px; top: 608px;
    background: var(--card-white);
  }
  .side-tab {
    position: absolute; left: -30px; top: 46px;
    width: 48px; height: 76px; border-radius: 50%;
    background: linear-gradient(180deg, var(--brand-mid), var(--green));
  }
  .person-name {
    position: absolute; left: 34px; top: 56px;
    color: var(--brand-blue); font-weight: 600; font-size: 26px; line-height: 1.2;
  }
  .person-title {
    position: absolute; left: 34px; top: 95px;
    color: var(--ink); font-size: 15.5px;
  }
  .address {
    position: absolute; left: 34px; top: 218px;
    color: var(--ink); font-size: 15.5px; line-height: 24px;
  }
  .contact-list {
    position: absolute; left: 34px; top: 281px;
    list-style: none; color: var(--ink); font-size: 15.5px;
  }
  .contact-list li { display: flex; align-items: center; height: 24px; white-space: nowrap; }
  .contact-list svg { width: 14px; height: 14px; margin-right: 18px; fill: var(--leaf-green); flex: none; }
  .back-brand {
    position: absolute; right: 34px; top: 180px;
    display: flex; flex-direction: column; align-items: center; gap: 14px;
  }
  .back-brand .brand-dot {
    width: 96px; height: 96px;
    background: var(--brand-blue); opacity: 1;
  }
  .card-back .brand-name { color: var(--brand-blue); font-size: 27px; text-align: center; }
</style>
</head>
<body>
  <section class="card card-front" aria-label="Card front">
    <div class="front-brand">
      <span class="brand-dot"></span>
      <div class="brand-name">Vorn Upkeep<br>KT Solar Venture</div>
    </div>
    <div class="services-band">
      <p>Solar Power System Install&nbsp; | &nbsp;Wiring, Rewinding &amp; Renovation</p>
      <p>Services &amp; Maintenance&nbsp; | &nbsp;Switch Board Upgrade&nbsp; | &nbsp;Power &amp; Lighting Point</p>
    </div>
    <div class="site-row">
      <span class="rule"></span>
      <span>www.ktsolarventure.com</span>
      <span class="rule"></span>
    </div>
  </section>

  <section class="card card-back" aria-label="Card back">
    <span class="side-tab"></span>
    <h1 class="person-name">Elias Marrow</h1>
    <p class="person-title">Managing Director</p>
    <p class="address">18 Harbour Lane, Wexley,<br>Fernvale, US 40217</p>
    <ul class="contact-list">
      <li><svg viewBox="0 0 16 16"><path d="M3 2h3l1.5 3.5-2 1.2a8 8 0 0 0 3.8 3.8l1.2-2L14 10v3a1 1 0 0 1-1 1A11 11 0 0 1 2 3a1 1 0 0 1 1-1z"/></svg>555-214-3690</li>
      <li><svg viewBox="0 0 16 16"><path d="M1 3h14v10H1z M2 4l6 5 6-5" fill="none" stroke="#2e8b3a" stroke-width="1.6"/></svg>elias@ktsolarventure.com</li>
      <li><svg viewBox="0 0 16 16"><circle cx="8" cy="8" r="6.5" fill="none" stroke="#2e8b3a" stroke-width="1.4"/><path d="M1.5 8h13M8 1.5c-3 3.5-3 9.5 0 13M8 1.5c3 3.5 3 9.5 0 13" fill="none" stroke="#2e8b3a" stroke-width="1.2"/></svg>www.ktsolarventure.com</li>
    </ul>
    <div class="back-brand">
      <span class="brand-dot"></span>
      <div class="brand-name">Vorn Upkeep<br>KT Solar Venture</div>
    </div>
  </section>
</body>
</html>
```